Tidemark Builders Business Card Design

We need a business card for an established builder of high quality bespoke homes in Auckland and Northland. We build and renovate homes collaboratively facilitating effective communication between owners, builders, architects, suppliers and tradespeople. We have never built or renovated a home that leaks or has faults. We only use reliable materials. We have never been sued or had legal action taken against us. We are honest builders of bespoke homes not group mass produced homes. Our niche market is in character homes. We practice sustainability and have built a lot of coastal property. We have been in business for over thirty years . We would like to see natural colors of the environment sand,sea and maybe vegetation . The design should communicate quality, sustainability,fair pricing, open communication and the originality of bespoke building. And the fact that the builder is registered.

Industry/Entity Type

Business

Contact Information for Business Card

Rowan Tellick Builders
Ph. 021583917
18 Kestrel Rd Harwood Bay Auckland 0814
PO Box 927 Mangawhai 0583

```html
<!DOCTYPE html>
<html lang="en">
<head>
<meta charset="utf-8">
<title>Tidemark Builders – Business Card</title>
<link rel="stylesheet" href="https://fonts.googleapis.com/css2?family=Open+Sans:wght@400;600;700&display=swap">
<style>
  :root {
    --backdrop: #d9d9d7;
    --card-black: #0e0e0e;
    --card-edge: #1c1c1c;
    --brand-white: #ffffff;
    --brand-red: #b3242a;
    --contact-grey: #b9b9b9;
    --rule-grey: #3a3a3a;
  }
  * { box-sizing: border-box; margin: 0; padding: 0; }
  html, body {
    width: 1200px;
    height: 900px;
    overflow: hidden;
    background: var(--backdrop);
    font-family: "Open Sans", Arial, sans-serif;
  }
  .stage {
    position: relative;
    width: 1200px;
    height: 900px;
  }
  .card {
    position: absolute;
    width: 640px;
    height: 366px;
    background: radial-gradient(ellipse at 40% 30%, var(--card-edge), var(--card-black) 70%);
    box-shadow: 0 10px 24px rgba(0,0,0,0.25);
  }
  .card--front { left: 380px; top: 70px; }
  .card--back  { left: 170px; top: 470px; }

  /* Front */
  .front-brand {
    position: absolute;
    inset: 0;
    display: flex;
    align-items: center;
    justify-content: center;
    gap: 14px;
  }
  .front-brand__mark {
    width: 18px;
    height: 18px;
    background: var(--brand-white);
  }
  .front-brand__name {
    color: var(--brand-white);
    font-weight: 700;
    font-size: 46px;
    letter-spacing: 0.5px;
  }

  /* Back */
  .back-brand {
    position: absolute;
    right: 58px;
    top: 62px;
    display: flex;
    align-items: center;
    gap: 10px;
  }
  .back-brand__mark {
    width: 14px;
    height: 14px;
    background: var(--brand-red);
  }
  .back-brand__name {
    color: var(--brand-red);
    font-weight: 700;
    font-size: 36px;
  }
  .holder {
    position: absolute;
    left: 46px;
    top: 140px;
    right: 58px;
    display: flex;
    align-items: flex-end;
    gap: 12px;
  }
  .holder__name {
    color: var(--brand-red);
    font-weight: 600;
    font-size: 17px;
    white-space: nowrap;
  }
  .holder__rule {
    flex: 1;
    height: 1px;
    background: var(--rule-grey);
    margin-bottom: 4px;
  }
  .contact {
    position: absolute;
    right: 58px;
    top: 232px;
    width: 330px;
    text-align: right;
    color: var(--contact-grey);
    font-size: 16px;
    line-height: 22px;
  }
  .contact__rule {
    height: 1px;
    background: var(--rule-grey);
    margin-bottom: 10px;
  }
  .contact__phone {
    display: flex;
    justify-content: flex-end;
    align-items: center;
    gap: 10px;
  }
  .contact__icon { width: 13px; height: 13px; }
</style>
</head>
<body>
<main class="stage">
  <section class="card card--front" aria-label="Card front">
    <div class="front-brand">
      <span class="front-brand__mark"></span>
      <span class="front-brand__name">Tidemark Builders</span>
    </div>
  </section>

  <section class="card card--back" aria-label="Card back">
    <div class="back-brand">
      <span class="back-brand__mark"></span>
      <span class="back-brand__name">Tidemark Builders</span>
    </div>
    <div class="holder">
      <span class="holder__name">Rowan Tellick Builders</span>
      <span class="holder__rule"></span>
    </div>
    <address class="contact" style="font-style:normal">
      <div class="contact__rule"></div>
      <div class="contact__phone">
        <span>021583917</span>
        <svg class="contact__icon" viewBox="0 0 24 24" aria-hidden="true">
          <path fill="var(--brand-red)" d="M6.6 10.8a15.1 15.1 0 0 0 6.6 6.6l2.2-2.2a1 1 0 0 1 1-.25 11.4 11.4 0 0 0 3.6.57 1 1 0 0 1 1 1V20a1 1 0 0 1-1 1A17 17 0 0 1 3 4a1 1 0 0 1 1-1h3.5a1 1 0 0 1 1 1c0 1.25.2 2.45.57 3.57a1 1 0 0 1-.25 1z"/>
        </svg>
      </div>
      <div>18 Kestrel Rd Harwood Bay</div>
      <div>Auckland 0814</div>
      <div>PO Box 927 Mangawhai 0583</div>
    </address>
  </section>
</main>
</body>
</html>
```